Bootstrap Website for Sports Technology Company

Create Bootstrap compatible, HTML and CSS stylesheet-based design templates for typography, forms, buttons, charts, navigation and other interface components for the www.tallow-pinery.com website. All designs should be Responsive CSS and Fluid.
We are transitioning www.tallow-pinery.com from Wordpress to Bootstrap and are looking for a fresh, clean landing page with navigation to other page styles. Official Colors and font are attached. Designer may recommend button styles, menu navigation, header, footer, etc. Please incorporate the graphic elements found on the tallow-pinery.com website.
Page Styles required:
- Landing Page
- Secondary Landing Page
- Five different Page Styles
- small, medium and large buttons
Designers are encouraged to submit the landing page with navigation. We will comment quickly to help with finalizing the design for final selection.
Industry/Entity Type
It Company
Look and feel
Each slider illustrates characteristics of the customer's brand and the style your logo design should communicate.

```html
<!DOCTYPE html>
<html lang="en">
<head>
<meta charset="utf-8">
<title>Tallow Pinery</title>
<link href="https://fonts.googleapis.com/css2?family=Arimo:ital,wght@0,400;0,700;1,400&display=swap" rel="stylesheet">
<style>
:root{
  --blue:#2f63a8;
  --hero:#4da2f2;
  --text:#444;
  --muted:#777;
  --rule:#dcdcdc;
  --footer:#f1f1f1;
  --dark:#2b2b2b;
  --link:#2a5a9c;
}
*{box-sizing:border-box;margin:0;padding:0}
html,body{width:836px;height:1200px;overflow:hidden}
body{position:relative;font-family:"Arimo",Arial,sans-serif;color:var(--text);background:#fff}
.abs{position:absolute}
.header{left:0;top:0;width:836px;height:121px;background:linear-gradient(#f2f2f2,#fff)}
.brand{left:64px;top:28px;display:flex;align-items:center;gap:8px;font-size:22px;font-weight:700;color:var(--blue)}
.brand .mark{width:30px;height:30px;border-radius:50%;background:#8a8a8a}
.social-top{top:28px;width:17px;height:17px;border-radius:3px}
.search{left:656px;top:26px;width:117px;height:20px;border:1px solid #ccc;background:#fff;font-size:8px;padding:5px 8px;color:#333}
.search svg{position:absolute;right:6px;top:4px}
.nav{left:432px;top:76px;display:flex;gap:0;font-size:10.4px;color:#333}
.nav span{margin-right:27px}
.nav .active{color:#111}
.nav-rule{left:432px;top:100px;width:341px;height:3px;background:#ccc}
.nav-active{left:432px;top:98px;width:33px;height:5px;background:var(--blue)}
.hero{left:0;top:121px;width:836px;height:289px;background:var(--hero)}
.hero h1{left:63px;top:171px;font-size:16.5px;color:#fff;font-weight:700}
.hero p{left:63px;top:200px;width:318px;font-size:10.2px;line-height:16px;color:#fff}
.cta{left:63px;top:293px;width:218px;height:38px;background:linear-gradient(#f3f3f3,#c9c9c9);border-radius:2px;box-shadow:0 1px 2px rgba(0,0,0,.3);font-size:12px;font-weight:700;color:#333;display:flex;align-items:center;padding-left:10px;gap:9px}
.cta i{width:13px;height:13px;border-radius:50%;background:#777;display:inline-block}
.dot{top:383px;width:10px;height:10px;border-radius:50%;background:#333}
.dot.on{background:#fff;border:2px solid #333}
.hero-photo{left:350px;top:160px;width:436px;height:250px;background:linear-gradient(120deg,#4da2f2 0%,#cfe0b8 55%,#b7cf9c 100%);border-radius:40% 20% 0 0}
.section-title{font-size:14.5px;font-weight:700;color:var(--blue)}
.how-title{left:0;top:424px;width:836px;text-align:center}
.col-rule{width:1px;background:#e6e6e6}
.step-icon{top:450px;height:80px;display:flex;align-items:center;gap:10px}
.step-icon .word{writing-mode:vertical-rl;transform:rotate(180deg);font-size:17px;color:#666}
.step-icon .art{width:55px;height:76px;background:#d9d9d9;border-radius:6px}
.step-text{top:545px;width:214px;font-size:10.2px;line-height:16px;color:#444}
.hr{left:63px;width:711px;height:1px;background:var(--rule)}
.about-title{left:63px;top:654px}
.about p{left:63px;width:512px;font-size:10.2px;line-height:16px;color:#444;text-align:justify}
.share{top:825px;height:15px;font-size:8px;display:flex;align-items:center;padding:0 5px;border-radius:2px;font-weight:700}
.about-art{left:596px;top:655px;width:160px;height:190px;background:linear-gradient(#f7f7f7,#e4e4e4);border-radius:8px}
.quote{top:888px;width:206px;font-style:italic;font-size:11.3px;line-height:19px;color:#222}
.author{top:953px;font-size:9.5px;color:var(--link)}
.footer{left:0;top:987px;width:836px;height:169px;background:var(--footer);border-top:2px solid #ddd}
.f-head{top:1003px;font-size:12px;color:#444}
.links{top:1030px;list-style:none;font-size:8.8px;color:#888;line-height:20.3px}
.links li:before{content:"\2022";color:#aaa;margin-right:5px}
.field{left:437px;width:158px;height:20px;border:1px solid #ccc;background:#fff;font-size:8px;padding:5px 11px;color:#333}
.submit{left:547px;top:1090px;width:48px;height:20px;background:#6d6d6d;color:#fff;font-size:10px;font-weight:700;display:flex;align-items:center;justify-content:center;border-radius:2px}
.pay{top:1126px;width:20px;height:13px;border-radius:2px;border:1px solid #bbb;background:#fff}
.conn-icon{left:630px;width:20px;height:20px;border-radius:3px}
.conn-text{left:665px;font-size:9px;color:#888}
.conn-text b{font-weight:400;font-size:10.4px;margin-left:3px}
.bottom{left:0;top:1156px;width:836px;height:44px;background:var(--dark);color:#aaa;font-size:8.8px;display:flex;align-items:center;justify-content:center}
</style>
</head>
<body>

<header class="abs header"></header>
<div class="abs brand"><span class="mark"></span>Tallow Pinery</div>
<span class="abs social-top" style="left:602px;background:#3b5998"></span>
<span class="abs social-top" style="left:623px;background:#3fb4e5"></span>
<div class="abs search">Search
  <svg width="11" height="11" viewBox="0 0 11 11"><circle cx="4.5" cy="4.5" r="3.3" fill="none" stroke="#222" stroke-width="1.6"/><line x1="7" y1="7" x2="10" y2="10" stroke="#222" stroke-width="2"/></svg>
</div>
<nav class="abs nav">
  <span class="active">Home</span><span>About us</span><span>World</span><span>Golf</span><span>Clubhouse</span><span style="margin-right:0">Support</span>
</nav>
<div class="abs nav-rule"></div>
<div class="abs nav-active"></div>

<section class="abs hero"></section>
<div class="abs hero-photo" role="img" aria-label="Photo of a golfer in a light green sweater mid-swing"></div>
<h1 class="abs" style="left:63px;top:171px;font-size:16.5px;color:#fff;font-weight:700">Welcome to Tallow Pinery</h1>
<p class="abs" style="left:63px;top:200px;width:318px;font-size:10.2px;line-height:16px;color:#fff;text-align:justify">Donec pulvinar eros vitae sagittis cursus. Donec vitae egestas eros. Praesent accumsan aliquet nibh, vitae porta nisl cursus vel. Pellentesque placerat nisl at lorem tincidunt, quis mollis ipsum elementum. Integer venenatis consequat nisl sit amet ultrices. Pellentesque vestibulum eget neque ac eleifend.</p>
<div class="abs cta"><i></i>Become a Tallow Pinery Fan today!</div>
<span class="abs dot on" style="left:64px"></span>
<span class="abs dot" style="left:85px"></span>
<span class="abs dot" style="left:104px"></span>
<span class="abs dot" style="left:123px"></span>

<h2 class="abs section-title how-title">How it works</h2>
<div class="abs col-rule" style="left:293px;top:455px;height:155px"></div>
<div class="abs col-rule" style="left:545px;top:455px;height:155px"></div>

<div class="abs step-icon" style="left:132px"><span class="word">Collect</span><span class="art" role="img" aria-label="Golfer silhouette addressing the ball"></span></div>
<div class="abs step-icon" style="left:376px"><span class="word">Analyze</span><span class="art" role="img" aria-label="Analysis emblem"></span></div>
<div class="abs step-icon" style="left:616px"><span class="word">Instruct</span><span class="art" role="img" aria-label="Sensor device emitting signal waves" style="width:95px"></span></div>

<p class="abs step-text" style="left:65px">Phasellus sed feugiat nisl. Curabitur commodo tincidunt vestibulum. Ut condimentum sapien lorem, ut consequat risus sollicitudin non. Suspendisse sed vestibulum sem.</p>
<p class="abs step-text" style="left:316px">Phasellus sed feugiat nisl. Curabitur commodo tincidunt vestibulum. Ut condimentum sapien lorem, ut consequat risus sollicitudin non. Suspendisse sed vestibulum sem.</p>
<p class="abs step-text" style="left:563px">Phasellus sed feugiat nisl. Curabitur commodo tincidunt vestibulum. Ut condimentum sapien lorem, ut consequat risus sollicitudin non. Suspendisse sed vestibulum sem.</p>

<div class="abs hr" style="top:634px"></div>

<section class="about">
  <h2 class="abs section-title about-title">About Tallow Pinery</h2>
  <p class="abs" style="top:681px">Donec a fermentum turpis, at fermentum mi. Aenean vehicula nisl justo, in mollis lorem hendrerit at. Morbi in luctus diam. Nam vestibulum dolor sit amet sollicitudin sollicitudin. Pellentesque rutrum vehicula nisl. Integer fermentum, nibh eget consectetur mollis, diam mauris venenatis sem, in tincidunt tellus eros nec nulla. Maecenas eget felis id tellus ultricies scelerisque sit amet nec tellus. Ut massa massa, bibendum et porta vel, porta adipiscing arcu. Nullam lacinia cursus nibh, quis dictum sem laoreet nec.</p>
  <p class="abs" style="top:767px">Praesent placerat nisi vel orci faucibus, eu eleifend quam tristique. Donec sodales cursus ipsum at rutrum. Maecenas commodo lectus volutpat rutrum sagittis. Nunc rutrum egestas libero, imperdiet laoreet erat consectetur vel. Sed id fringilla justo.</p>
</section>
<span class="abs share" style="left:63px;width:43px;background:#3b5998;color:#fff">Share</span>
<span class="abs share" style="left:110px;width:44px;background:#3fa3dc;color:#fff">Post</span>
<span class="abs share" style="left:158px;width:44px;border:1px solid #bbb;background:#fff;color:#222">Share</span>
<span class="abs share" style="left:206px;width:44px;border:1px solid #bbb;background:#f4f4f4;color:#555;font-weight:400">Email</span>
<span class="abs share" style="left:254px;width:31px;border:1px solid #bbb;background:#eef2f8;color:#3b5998;font-weight:400">Like</span>
<span class="abs share" style="left:288px;width:18px;border:1px solid #bbb;background:#fff;color:#333;font-weight:400">13</span>
<div class="abs about-art" role="img" aria-label="Line drawing of a golfer with a bag and sensor"></div>

<div class="abs hr" style="top:867px"></div>
<div class="abs col-rule" style="left:293px;top:875px;height:110px"></div>
<div class="abs col-rule" style="left:545px;top:875px;height:110px"></div>

<p class="abs quote" style="left:79px">" Our Members found Dale Whitcombe, Tour professional, informative and highly educational during a recent golf... "</p>
<p class="abs author" style="left:77px">- Morgan Fenwick</p>
<p class="abs quote" style="left:324px">" Our Members found Dale Whitcombe, Tour professional, informative and highly educational during a recent golf... "</p>
<p class="abs author" style="left:322px">- Morgan Fenwick</p>
<p class="abs quote" style="left:567px">" Our Members found Dale Whitcombe, Tour professional, informative and highly educational during a recent golf... "</p>
<p class="abs author" style="left:565px">- Morgan Fenwick</p>

<footer class="abs footer"></footer>
<div class="abs col-rule" style="left:419px;top:1000px;height:145px;background:#d8d8d8"></div>
<div class="abs col-rule" style="left:611px;top:1000px;height:145px;background:#d8d8d8"></div>

<h3 class="abs f-head" style="left:64px;font-weight:400">Quick Links</h3>
<ul class="abs links" style="left:64px"><li>Integer lobortis</li><li>Curabitur ac</li><li>Phasellus tellus nisl</li><li>Aenean fringilla</li><li>Vestibulum</li><li>Aliquam commodo</li></ul>
<ul class="abs links" style="left:188px"><li>Integer lobortis</li><li>Curabitur ac</li><li>Phasellus tellus nisl</li><li>Aenean fringilla</li><li>Vestibulum</li><li>Aliquam commodo</li></ul>
<ul class="abs links" style="left:312px"><li>Integer lobortis</li><li>Curabitur ac</li><li>Phasellus tellus nisl</li><li>Aenean fringilla</li><li>Vestibulum</li><li>Aliquam commodo</li></ul>

<h3 class="abs f-head" style="left:437px;font-weight:400">Email Signup</h3>
<div class="abs field" style="top:1032px">Name</div>
<div class="abs field" style="top:1062px">Email ID</div>
<div class="abs submit">SUBMIT</div>
<span class="abs pay" style="left:466px"></span>
<span class="abs pay" style="left:492px"></span>
<span class="abs pay" style="left:519px"></span>
<span class="abs pay" style="left:545px"></span>
<span class="abs pay" style="left:572px"></span>

<h3 class="abs f-head" style="left:630px;font-weight:400">Connect with us</h3>
<span class="abs conn-icon" style="top:1032px;background:#3b5998"></span>
<span class="abs conn-text" style="top:1035px">Join with us on <b style="color:#2a5a9c">Friendwall</b></span>
<span class="abs conn-icon" style="top:1061px;background:#3fb4e5"></span>
<span class="abs conn-text" style="top:1064px">Follow us on <b style="color:#2b9fd6">Chirper</b></span>
<span class="abs conn-icon" style="top:1090px;background:#1b6fa8"></span>
<span class="abs conn-text" style="top:1093px">Share on <b style="color:#1b6fa8">WorkLink</b></span>
<span class="abs conn-icon" style="top:1119px;background:#c4302b"></span>
<span class="abs conn-text" style="top:1122px">Watch on <b style="color:#b22b26">ClipReel</b></span>

<div class="abs bottom">Copyright © 2013 &nbsp;www.tallow-pinery.com &nbsp;All rights reserved.</div>

</body>
</html>
```